Belmont Ridge Business Card Design Project

We have recently rebranded and would like to design new business cards that incorporate the corporate logo - double sided cards with corporate logo on one side and contact details on the other

Target Market(s)

Sophisticated and high net worth investors and finance industry professionals

Industry/Entity Type

Funds Management

Contact Information for Business Card

The card should prominently feature the company name and logo. Other details will be standard contact details for each staff member - name, address, phone, email, website

Colors
0054AA
0677BA
7BADD7
CADEEF
E8F1F8

Requirements
Must have
• Double-sided design with one side prominently featuring the corporate logo and the other side with all standard contact details

```html
<!DOCTYPE html>
<html lang="en">
<head>
<meta charset="utf-8">
<title>Belmont Ridge — Business Card</title>
<link rel="stylesheet" href="https://fonts.googleapis.com/css2?family=Cinzel:wght@500&family=Arimo:wght@400;700&display=swap">
<style>
  :root {
    --navy: #1f4677;
    --paper: #ffffff;
    --backdrop: #e4e4e2;
    --ink-grey: #6b6b6b;
    --rule-grey: #9a9a9a;
    --card-w: 520px;
    --card-h: 297px;
  }
  * { box-sizing: border-box; margin: 0; padding: 0; }
  html, body {
    width: 1200px; height: 802px; overflow: hidden;
    background: var(--backdrop);
  }
  .sheet {
    width: 1200px; height: 802px;
    display: flex; align-items: center; justify-content: center; gap: 60px;
  }
  .card {
    width: var(--card-w); height: var(--card-h);
    position: relative;
    box-shadow: 0 6px 18px rgba(0,0,0,.12);
  }
  .card--front { background: var(--paper); display: flex; }
  .card--back { background: var(--navy); }

  .brand {
    width: 255px; display: flex; align-items: center; justify-content: center;
  }
  .brand__name {
    font-family: "Cinzel", serif; font-weight: 500;
    color: var(--navy); font-size: 25px; letter-spacing: 1px;
  }
  .divider {
    width: 1px; background: var(--rule-grey);
    margin: 55px 0 55px;
  }
  .details {
    padding: 58px 0 0 26px;
    font-family: "Arimo", sans-serif; color: var(--ink-grey);
  }
  .details__name {
    color: var(--navy); font-weight: 700; font-size: 17px; letter-spacing: .3px;
  }
  .details__role { font-size: 13px; margin-top: 2px; }
  .details__address { font-size: 13px; line-height: 1.35; margin-top: 14px; }
  .contact-list { list-style: none; margin-top: 12px; font-size: 13px; line-height: 1.55; }
  .contact-list li { display: flex; align-items: center; gap: 8px; }
  .contact-list svg { width: 11px; height: 11px; flex: none; }

  .card--back .back__name {
    position: absolute; left: 0; right: 0; top: 112px; text-align: center;
    font-family: "Cinzel", serif; font-weight: 500;
    color: #e9ecef; font-size: 44px; letter-spacing: 2px;
  }
</style>
</head>
<body>
<main class="sheet">
  <section class="card card--front" aria-label="Business card, contact side">
    <div class="brand">
      <span class="brand__name">Belmont Ridge</span>
    </div>
    <div class="divider"></div>
    <div class="details">
      <p class="details__name">DANIEL HARTLEY</p>
      <p class="details__role">Manager</p>
      <p class="details__address">Your Address, City<br>State, Zip 0000</p>
      <ul class="contact-list">
        <li>
          <svg viewBox="0 0 12 12" aria-hidden="true"><circle cx="6" cy="6" r="6" fill="#1f4677"/><path d="M4 3.2l1 1.4-.6.7a3.4 3.4 0 0 0 2.3 2.3l.7-.6 1.4 1-.6.9C6 8.9 3.1 6 3.1 3.8z" fill="#fff"/></svg>
          555-014-2100
        </li>
        <li>
          <svg viewBox="0 0 12 12" aria-hidden="true"><rect x="0.5" y="2" width="11" height="8" fill="#1f4677"/><path d="M1 2.6L6 6.6l5-4" stroke="#fff" stroke-width="1" fill="none"/></svg>
          dhartley@belmontridge.com
        </li>
        <li>
          <svg viewBox="0 0 12 12" aria-hidden="true"><circle cx="6" cy="6" r="6" fill="#1f4677"/><circle cx="6" cy="6" r="3.6" stroke="#fff" stroke-width=".8" fill="none"/><path d="M2.4 6h7.2M6 2.4v7.2" stroke="#fff" stroke-width=".8"/></svg>
          www.belmontridge.com
        </li>
      </ul>
    </div>
  </section>

  <section class="card card--back" aria-label="Business card, brand side">
    <p class="back__name">Belmont Ridge</p>
  </section>
</main>
</body>
</html>
```